Vantiqo custom business card design

Need a authentic, innovative business card design for a new mobile app business. I am uploading a few screen images from our app for you to view. I would like app design theme to match business card design. I can also send logo images.

```html
<!DOCTYPE html>
<html lang="en">
<head>
<meta charset="utf-8">
<title>Vantiqo Business Card</title>
<link rel="stylesheet" href="https://fonts.googleapis.com/css2?family=Poppins:wght@600;800&family=Questrial&display=swap">
<style>
  :root {
    --bg: #ece9ee;
    --purple: #5d2a8b;
    --ink: #262626;
    --muted: #3a3a3a;
    --white: #ffffff;
    --rule: #2f2f2f;
  }
  html, body {
    margin: 0;
    padding: 0;
    width: 1200px;
    height: 831px;
    overflow: hidden;
    background: var(--bg);
  }
  .canvas {
    position: relative;
    width: 1200px;
    height: 831px;
  }
  .card {
    position: absolute;
    width: 520px;
    height: 300px;
    border-radius: 3px;
    box-shadow: 0 8px 24px rgba(0,0,0,0.18);
    overflow: hidden;
  }
  .card-front {
    left: 60px;
    top: 130px;
    background: var(--purple);
    display: flex;
    flex-direction: column;
    align-items: center;
    justify-content: center;
    gap: 14px;
  }
  .brand-mark {
    border-radius: 50%;
  }
  .card-front .brand-mark {
    width: 92px;
    height: 92px;
    background: var(--white);
  }
  .brand-name {
    font-family: "Poppins", sans-serif;
    font-weight: 800;
    letter-spacing: 0.5px;
    line-height: 1;
  }
  .card-front .brand-name {
    color: var(--white);
    font-size: 44px;
  }
  .card-back {
    left: 620px;
    top: 400px;
    background: var(--white);
  }
  .back-brand {
    position: absolute;
    left: 0;
    top: 0;
    width: 240px;
    height: 300px;
    display: flex;
    flex-direction: column;
    align-items: center;
    justify-content: center;
    gap: 12px;
  }
  .back-brand .brand-mark {
    width: 74px;
    height: 74px;
    background: var(--purple);
  }
  .back-brand .brand-name {
    color: var(--ink);
    font-size: 34px;
  }
  .divider {
    position: absolute;
    left: 250px;
    top: 72px;
    width: 1.5px;
    height: 150px;
    background: var(--rule);
  }
  .contact {
    position: absolute;
    left: 276px;
    top: 90px;
  }
  .person-name {
    font-family: "Poppins", sans-serif;
    font-weight: 600;
    font-size: 24px;
    color: var(--purple);
    margin: 0;
    line-height: 1.05;
  }
  .person-title {
    font-family: "Questrial", sans-serif;
    font-size: 16px;
    color: var(--muted);
    margin: 2px 0 18px;
  }
  .contact-list {
    list-style: none;
    margin: 0;
    padding: 0;
    font-family: "Questrial", sans-serif;
    font-size: 17px;
    color: var(--ink);
  }
  .contact-list li {
    display: flex;
    align-items: center;
    gap: 10px;
    height: 22px;
  }
  .contact-list svg {
    width: 15px;
    height: 15px;
    flex: none;
    fill: var(--purple);
  }
</style>
</head>
<body>
<main class="canvas">
  <section class="card card-front" aria-label="Card front">
    <div class="brand-mark"></div>
    <div class="brand-name">Vantiqo</div>
  </section>

  <section class="card card-back" aria-label="Card back">
    <div class="back-brand">
      <div class="brand-mark"></div>
      <div class="brand-name">Vantiqo</div>
    </div>
    <div class="divider"></div>
    <div class="contact">
      <h1 class="person-name">Your Name</h1>
      <p class="person-title">Your Title</p>
      <ul class="contact-list">
        <li>
          <svg viewBox="0 0 24 24" aria-hidden="true"><path d="M6.6 10.8c1.4 2.8 3.8 5.1 6.6 6.6l2.2-2.2c.3-.3.7-.4 1-.2 1.1.4 2.3.6 3.6.6.6 0 1 .4 1 1V20c0 .6-.4 1-1 1C10.6 21 3 13.4 3 4c0-.6.4-1 1-1h3.5c.6 0 1 .4 1 1 0 1.3.2 2.5.6 3.6.1.3 0 .7-.2 1l-2.3 2.2z"/></svg>
          <span>123-456-2100</span>
        </li>
        <li>
          <svg viewBox="0 0 24 24" aria-hidden="true"><path d="M2 5h20v14H2V5zm2 2v.5l8 5 8-5V7H4zm0 2.8V17h16V9.8l-8 5-8-5z"/></svg>
          <span>youremail@mailbox.com</span>
        </li>
        <li>
          <svg viewBox="0 0 24 24" aria-hidden="true"><path d="M12 2a10 10 0 1 0 0 20 10 10 0 0 0 0-20zm6.9 6h-3a15 15 0 0 0-1.3-3.9A8 8 0 0 1 18.9 8zM12 4c.9 1.2 1.6 2.6 2 4h-4c.4-1.4 1.1-2.8 2-4zM4.3 14a8 8 0 0 1 0-4h3.4a16 16 0 0 0 0 4H4.3zm.8 2h3a15 15 0 0 0 1.3 3.9A8 8 0 0 1 5.1 16zm3-8h-3a8 8 0 0 1 4.3-3.9C8.8 5.3 8.4 6.6 8.1 8zM12 20c-.9-1.2-1.6-2.6-2-4h4c-.4 1.4-1.1 2.8-2 4zm2.3-6H9.7a14 14 0 0 1 0-4h4.6a14 14 0 0 1 0 4zm.3 5.9c.6-1.2 1-2.5 1.3-3.9h3a8 8 0 0 1-4.3 3.9zm1.7-5.9a16 16 0 0 0 0-4h3.4a8 8 0 0 1 0 4h-3.4z"/></svg>
          <span>www.yourwebsite.com</span>
        </li>
      </ul>
    </div>
  </section>
</main>
</body>
</html>
```